We are a recruitment company based in Norwich/Cambridge England.
I have included our company logo which we want to remain the same.

What we are looking for is a new creative Business card which will really stand out!!

Contact Information for Business Card

Harriet Dunmore
email: Harriet@plavex.co.uk
Address: Brackwell House
Fenmoor Enterprise Park
Partridge Way
Norwich
QB9 3KX
Tel:01632 960418

```html
<!DOCTYPE html>
<html lang="en">
<head>
<meta charset="utf-8">
<title>Plavex Business Card</title>
<link rel="stylesheet" href="https://fonts.googleapis.com/css2?family=Open+Sans:wght@400;600;700&display=swap">
<style>
  :root {
    --lime: #96c81e;
    --grey: #8b8689;
    --ink: #4a4a4a;
    --paper: #ffffff;
    --backdrop: #e9e6e3;
    --rule: #d9d9d9;
  }
  * { margin: 0; padding: 0; box-sizing: border-box; }
  html, body {
    width: 1200px;
    height: 997px;
    overflow: hidden;
    background: var(--backdrop);
    font-family: "Open Sans", Arial, sans-serif;
  }
  .card {
    position: absolute;
    width: 560px;
    height: 320px;
    background: var(--paper);
    box-shadow: 0 4px 14px rgba(0,0,0,0.10);
    overflow: hidden;
  }
  .card--contact { left: 70px; top: 150px; }
  .card--brand { left: 570px; top: 527px; }

  /* Contact side */
  .brand-mark {
    position: absolute;
    left: 70px;
    top: 88px;
    display: flex;
    align-items: center;
    gap: 12px;
  }
  .brand-mark__dot {
    width: 38px;
    height: 38px;
    border-radius: 50%;
    background: var(--lime);
  }
  .brand-mark__name {
    font-size: 40px;
    font-weight: 700;
    color: var(--grey);
    letter-spacing: -0.5px;
  }
  .divider {
    position: absolute;
    left: 292px;
    top: 32px;
    width: 1px;
    height: 150px;
    background: var(--rule);
  }
  .contact {
    position: absolute;
    left: 316px;
    top: 34px;
    color: var(--ink);
    font-size: 13px;
    line-height: 1.35;
  }
  .contact__name {
    color: var(--lime);
    font-weight: 700;
    font-size: 14px;
    text-transform: uppercase;
    letter-spacing: 0.3px;
  }
  .contact__role { margin-bottom: 6px; }
  .contact__line { display: flex; align-items: center; gap: 7px; }
  .contact__line svg { width: 10px; height: 10px; flex: none; }
  .contact__address { margin-top: 6px; padding-left: 17px; }
  .footer-band { position: absolute; left: 0; bottom: 0; width: 560px; height: 150px; }
  .footer-band__url {
    position: absolute;
    right: 112px;
    bottom: 34px;
    color: var(--paper);
    font-size: 13px;
    letter-spacing: 1.5px;
    transform: rotate(-13deg);
    transform-origin: right bottom;
  }

  /* Brand side */
  .lockup {
    position: absolute;
    left: 50%;
    top: 50%;
    transform: translate(-50%, -50%);
    display: flex;
    align-items: center;
    gap: 16px;
  }
  .lockup__dot {
    width: 52px;
    height: 52px;
    border-radius: 50%;
    background: var(--lime);
  }
  .lockup__text { display: flex; flex-direction: column; }
  .lockup__name {
    font-size: 56px;
    font-weight: 700;
    color: var(--grey);
    line-height: 1;
    letter-spacing: -1px;
  }
  .lockup__tagline {
    font-size: 11px;
    color: var(--grey);
    letter-spacing: 4px;
    margin-top: 4px;
  }
</style>
</head>
<body>

<section class="card card--contact">
  <div class="brand-mark">
    <span class="brand-mark__dot"></span>
    <span class="brand-mark__name">Plavex</span>
  </div>

  <div class="divider"></div>

  <div class="contact">
    <p class="contact__name">Harriet Dunmore</p>
    <p class="contact__role">Director</p>
    <p class="contact__line">
      <svg viewBox="0 0 10 10" aria-hidden="true"><path d="M2 0.5 L3.6 2.6 L2.8 3.6 Q4 6 6.4 7.2 L7.4 6.4 L9.5 8 L8.4 9.5 Q2 8.5 0.5 1.6 Z" fill="var(--lime)"/></svg>
      01632 960418
    </p>
    <p class="contact__line">
      <svg viewBox="0 0 10 10" aria-hidden="true"><rect x="0.5" y="2" width="9" height="6.5" fill="var(--lime)"/><path d="M0.5 2 L5 5.6 L9.5 2" stroke="#fff" stroke-width="0.9" fill="none"/></svg>
      Harriet@plavex.co.uk
    </p>
    <div class="contact__address">
      <p>Brackwell House</p>
      <p>Fenmoor Enterprise Park</p>
      <p>Partridge Way Norwich QB9 3KX</p>
    </div>
  </div>

  <svg class="footer-band" viewBox="0 0 560 150" preserveAspectRatio="none" aria-hidden="true">
    <path d="M0 150 L0 150 Q260 30 560 10 L560 16 Q270 40 0 150 Z" fill="var(--grey)"/>
    <path d="M0 150 Q280 36 560 18 L560 150 Z" fill="var(--lime)"/>
    <path d="M0 150 Q300 66 560 54 L560 150 Z" fill="var(--paper)"/>
  </svg>
  <span class="footer-band__url">www.plavex.co.uk</span>
</section>

<section class="card card--brand">
  <div class="lockup">
    <span class="lockup__dot"></span>
    <div class="lockup__text">
      <span class="lockup__name">Plavex</span>
      <span class="lockup__tagline">Technology Recruitment</span>
    </div>
  </div>
</section>

</body>
</html>
```